Indy Film Production Company/Studio

We need a business card designed from an existing logo. We are a digital studio/production company that caters to creating genre entertainment, like Action, Horror, and martial arts. The card along with the logo will be used to Brand the company from letter heads to banners. The design will also be used for postcards and Brochures. It should be professional and masculine.
Updates

Thank you to all the designers who have participated. I'm narrowing down who it will be. Thank you again.

Target Market(s)

Investors, Networks, Producers, and actors

Industry/Entity Type

Film Production

Contact Information for Business Card

Teodoro Valbuena
Producer/Writer/Director
www.kestrelpicturehouse.example

Requirements
Must have
• Website address, Facebook icon and Twitter icon possibly in the back of the card.
Nice to have
• Logline of Company: Follow The Action.

```html
<!DOCTYPE html>
<html lang="en">
<head>
<meta charset="utf-8">
<title>Kestrel Picture House – Business Card</title>
<link rel="stylesheet" href="https://fonts.googleapis.com/css2?family=Open+Sans:wght@300;400;700&display=swap">
<style>
  :root {
    --backdrop: #d8d3cb;
    --card-frost: #eceeee;
    --card-edge: #c9cccc;
    --brand-red: #c8151b;
    --brand-red-dark: #8f0c10;
    --band-black: #121212;
    --text-light: #f4f4f4;
    --text-soft: #f3c9c9;
    --contact-text: #d9d9d9;
  }
  * { margin: 0; padding: 0; box-sizing: border-box; }
  html, body {
    width: 1200px; height: 969px; overflow: hidden;
    background: var(--backdrop);
    font-family: "Open Sans", Arial, sans-serif;
  }
  .card {
    position: absolute; left: 150px; top: 228px;
    width: 900px; height: 512px;
    background: linear-gradient(160deg, #f6f7f7 0%, var(--card-frost) 60%, #e2e5e5 100%);
    border: 1px solid var(--card-edge);
    box-shadow: 0 18px 40px rgba(0,0,0,0.18);
  }
  .brand {
    position: absolute; left: 0; right: 0; top: 140px;
    display: flex; justify-content: center; align-items: center; gap: 18px;
  }
  .brand-mark {
    width: 30px; height: 30px; background: var(--brand-red);
  }
  .brand-name {
    font-weight: 700; font-size: 50px; letter-spacing: 1px;
    text-transform: uppercase; color: var(--brand-red);
  }
  .info-band {
    position: absolute; left: 0; top: 343px; width: 100%; height: 127px;
  }
  .info-band svg { position: absolute; inset: 0; }
  .person {
    position: absolute; left: 38px; top: 30px; color: var(--text-light);
  }
  .person-name {
    font-weight: 400; font-size: 29px; text-transform: uppercase; letter-spacing: 0.5px;
  }
  .person-role {
    font-weight: 300; font-size: 19px; text-transform: uppercase;
    color: var(--text-soft); margin-top: 2px;
  }
  .contacts {
    position: absolute; right: 26px; top: 17px;
    list-style: none; color: var(--contact-text);
    font-weight: 300; font-size: 21px; text-align: right;
  }
  .contacts li {
    display: flex; justify-content: flex-end; align-items: center; gap: 14px;
    height: 31px;
  }
  .contacts svg { width: 20px; height: 20px; flex: none; }
</style>
</head>
<body>
  <div class="card">
    <div class="brand">
      <span class="brand-mark"></span>
      <span class="brand-name">Kestrel Picture House</span>
    </div>

    <div class="info-band">
      <svg width="900" height="127" viewBox="0 0 900 127" aria-hidden="true">
        <defs>
          <linearGradient id="redBand" x1="0" y1="0" x2="0" y2="1">
            <stop offset="0" stop-color="#d91d23"/>
            <stop offset="1" stop-color="#a90f14"/>
          </linearGradient>
        </defs>
        <polygon points="0,0 496,0 444,127 0,127" fill="url(#redBand)"/>
        <polygon points="504,0 900,0 900,127 452,127" fill="var(--band-black)"/>
        <line x1="498" y1="0" x2="446" y2="127" stroke="#9a9a9a" stroke-width="3"/>
      </svg>

      <div class="person">
        <p class="person-name">Teodoro Valbuena</p>
        <p class="person-role">Producer/Writer/Director</p>
      </div>

      <ul class="contacts">
        <li>555 0142 7788
          <svg viewBox="0 0 20 20" aria-hidden="true"><path d="M2 7c0-3 3-4 8-4s8 1 8 4l-3 1-1-2c-2-.6-6-.6-8 0L5 8zM5 9h10l2 7H3z" fill="#eee"/><circle cx="10" cy="12.5" r="2" fill="#121212"/></svg>
        </li>
        <li>office@kestrelpicturehouse.example
          <svg viewBox="0 0 20 20" aria-hidden="true"><rect x="2" y="4" width="16" height="12" fill="#eee"/><path d="M2 4l8 7 8-7" fill="none" stroke="#121212" stroke-width="1.5"/></svg>
        </li>
        <li>www.kestrelpicturehouse.example
          <svg viewBox="0 0 20 20" aria-hidden="true"><circle cx="10" cy="10" r="8" fill="#eee"/><path d="M10 2v16M2 10h16M10 2c-4 4-4 12 0 16M10 2c4 4 4 12 0 16" fill="none" stroke="#121212" stroke-width="1.2"/></svg>
        </li>
      </ul>
    </div>
  </div>
</body>
</html>
```